Business card for Luxury Portable Restroom Trailer company

We are a Luxury Portable Restroom Trailer Company Called FALCRIDGE HIRES. Based in Orange County California. We provide portable restroom trailers for events, such as, Weddings, Concerts, Charity events, Sporting events, Tournaments, Corporate events, ect. We rent and Sell the Luxury restrooms. Our colors are white, grey, and Orange. As you will see in the logo we uploaded.
There are 2 people in the company so the names and titles will change for the 3 people but card will remain the same. Here is the information for each Person: Dwight Penner CFO 555 318-0476
next Person: Leon Marchetti VP 555 318-0476
Next Person: Owen Marchetti CEO 555 318-0476
Information to include on the card: Luxury Restroom Trailers Rental and Sales. Weddings, Concerts, Charity, Sporting and Corp. Events.

```html
<!DOCTYPE html>
<html lang="en">
<head>
<meta charset="utf-8">
<title>Falcridge Hires — Business Card</title>
<link rel="stylesheet" href="https://fonts.googleapis.com/css2?family=Montserrat:wght@400;500;700;800&display=swap">
<style>
  :root {
    --orange: #f26c23;
    --grey: #5f5f61;
    --white: #ffffff;
    --ink: #1d1d1f;
    --backdrop: #e9e9eb;
  }
  * { box-sizing: border-box; margin: 0; padding: 0; }
  html, body { width: 1200px; height: 880px; overflow: hidden; }
  body {
    background: var(--backdrop);
    font-family: "Montserrat", Arial, sans-serif;
    position: relative;
  }
  .card {
    position: absolute;
    width: 620px;
    height: 354px;
    overflow: hidden;
    box-shadow: 0 10px 28px rgba(0,0,0,0.18);
  }
  /* Front */
  .card-front {
    left: 60px; top: 60px;
    background: var(--orange);
    color: var(--white);
  }
  .card-front .brand {
    position: absolute;
    left: 0; right: 0; top: 92px;
    display: flex; align-items: center; justify-content: center; gap: 14px;
  }
  .brand-mark {
    width: 22px; height: 22px;
    background: currentColor;
  }
  .brand-name {
    font-weight: 800;
    font-size: 44px;
    letter-spacing: 1px;
    line-height: 1;
  }
  .services {
    position: absolute;
    left: 0; right: 0; top: 230px;
    text-align: center;
    font-weight: 500;
    font-size: 15px;
    line-height: 1.75;
  }
  .services .dot { display: inline-block; width: 8px; height: 8px; border-radius: 50%; background: var(--white); margin: 0 8px 2px; vertical-align: middle; }
  /* Back */
  .card-back {
    left: 520px; top: 466px;
    background: var(--white);
  }
  .card-back .swoosh { position: absolute; inset: 0; }
  .card-back .brand {
    position: absolute;
    right: 34px; top: 62px;
    display: flex; align-items: center; gap: 10px;
    color: var(--grey);
  }
  .card-back .brand-name { font-size: 30px; }
  .card-back .brand-mark { width: 16px; height: 16px; }
  .team {
    position: absolute;
    left: 36px; top: 70px;
    list-style: none;
  }
  .member { margin-bottom: 10px; }
  .member-name {
    color: var(--orange);
    font-weight: 700;
    font-size: 19px;
    letter-spacing: 0.5px;
    text-transform: uppercase;
    line-height: 1.2;
  }
  .member-title { color: var(--ink); font-size: 14px; margin-left: 14px; line-height: 1.35; }
  .member-phone {
    color: var(--ink); font-size: 14px; margin-left: 28px;
    display: flex; align-items: center; gap: 6px; line-height: 1.35;
  }
  .member-phone svg { width: 15px; height: 15px; fill: var(--orange); }
</style>
</head>
<body>

<section class="card card-front" aria-label="Card front">
  <div class="brand">
    <span class="brand-mark"></span>
    <span class="brand-name">FALCRIDGE HIRES</span>
  </div>
  <p class="services">
    <span class="dot"></span>Luxury Restroom Trailers Rental and Sales<br>
    <span class="dot"></span>Weddings <span class="dot"></span>Concerts <span class="dot"></span>Charity <span class="dot"></span>Sporting and Corp <span class="dot"></span>Events
  </p>
</section>

<section class="card card-back" aria-label="Card back">
  <svg class="swoosh" viewBox="0 0 620 354" preserveAspectRatio="none" aria-hidden="true">
    <path d="M220 354 C 380 320, 520 250, 620 150 L620 354 Z" fill="var(--orange)"/>
    <path d="M250 330 C 400 290, 530 220, 620 135" fill="none" stroke="var(--grey)" stroke-width="5"/>
  </svg>
  <div class="brand">
    <span class="brand-mark"></span>
    <span class="brand-name">FALCRIDGE HIRES</span>
  </div>
  <ul class="team">
    <li class="member">
      <p class="member-name">Dwight Penner</p>
      <p class="member-title">CFO</p>
      <p class="member-phone"><svg viewBox="0 0 24 24" aria-hidden="true"><path d="M3 9c0-3 4-5 9-5s9 2 9 5v2h-5V9H8v2H3z M6 12h12l2 8H4z"/></svg>555 318-0476</p>
    </li>
    <li class="member">
      <p class="member-name">Leon Marchetti</p>
      <p class="member-title">VP</p>
      <p class="member-phone"><svg viewBox="0 0 24 24" aria-hidden="true"><path d="M3 9c0-3 4-5 9-5s9 2 9 5v2h-5V9H8v2H3z M6 12h12l2 8H4z"/></svg>555 318-0476</p>
    </li>
    <li class="member">
      <p class="member-name">Owen Marchetti</p>
      <p class="member-title">CEO</p>
      <p class="member-phone"><svg viewBox="0 0 24 24" aria-hidden="true"><path d="M3 9c0-3 4-5 9-5s9 2 9 5v2h-5V9H8v2H3z M6 12h12l2 8H4z"/></svg>555 318-0476</p>
    </li>
  </ul>
</section>

</body>
</html>
```